Business Card Design for Flood Rescue 360 - Property Restoration Professionals

I need a business card designed for Flood Rescue 360. We are a full-service property restoration solution. Providing water, fire, smoke & storm restoration as well as mold remediation and full remodel or reconstruction to homes and businesses across Dallas-Fort Worth, TX.
Target Market(s)
home and business owners with insurance covered property damage from water, fire or storm related damage
Industry/Entity Type
property restoration
Contact Information for Business Card
Marcus Pelley General Manager Cell: 214-555-0193 Office: 469-555-0148 email: Marcus@FloodRescue360.example services: Water, Fire, Mold, Reconstruction Tagline: Urgency for Your Water Emergency!
Look and feel
Each slider illustrates characteristics of the customer's brand and the style your logo design should communicate.

```html
<!DOCTYPE html>
<html lang="en">
<head>
<meta charset="utf-8">
<title>Flood Rescue 360 – Business Card</title>
<link href="https://fonts.googleapis.com/css2?family=Montserrat:wght@400;500;700;800&display=swap" rel="stylesheet">
<style>
  :root{
    --bg:#e9e7e4;
    --white:#ffffff;
    --ink:#161616;
    --black:#111111;
    --blue:#13a5e0;
  }
  *{margin:0;padding:0;box-sizing:border-box}
  html,body{width:1200px;height:768px;overflow:hidden;background:var(--bg);font-family:'Montserrat',sans-serif}
  .canvas{position:relative;width:1200px;height:768px}
  .card{position:absolute;top:230px;width:540px;height:309px;overflow:hidden;box-shadow:0 10px 30px rgba(0,0,0,.18)}
  .card--front{left:40px;background:var(--white)}
  .card--back{left:620px;background:var(--black)}
  .front-swoosh{position:absolute;inset:0}
  .brand{position:absolute;left:30px;top:128px;display:flex;align-items:center;gap:8px;white-space:nowrap;color:var(--blue);font-weight:700;font-size:18px}
  .brand-mark{width:12px;height:12px;border-radius:50%;background:var(--blue);flex:none}
  .divider{position:absolute;left:232px;top:90px;width:2px;height:112px;background:var(--blue)}
  .contact{position:absolute;left:248px;top:88px;color:var(--ink);white-space:nowrap}
  .contact__name{color:var(--blue);font-weight:800;font-size:24px;letter-spacing:.2px}
  .contact__title{font-size:12.5px;font-weight:500;margin:2px 0 9px}
  .contact__row{display:flex;align-items:center;gap:8px;font-size:12.5px;font-weight:500;margin-bottom:5px}
  .contact__row svg{width:12px;height:12px;fill:var(--blue);flex:none}
  .services{position:absolute;left:150px;bottom:18px;color:var(--white);font-size:12.5px;font-weight:500;letter-spacing:.3px;white-space:nowrap}
  .services .dot{color:var(--blue);margin:0 3px}
  .pattern{position:absolute;inset:0;background:radial-gradient(ellipse at 20% 15%,#3a3a3a 0%,#1d1d1d 45%,#0f0f0f 100%)}
  .tagline{position:absolute;left:120px;right:24px;bottom:70px;display:flex;align-items:center;justify-content:space-between;gap:14px;white-space:nowrap;color:var(--blue);font-weight:700;font-size:15px}
  .tagline__brand{display:flex;align-items:center;gap:6px;font-size:15px;font-weight:700}
  .tagline__brand .brand-mark{width:10px;height:10px}
</style>
</head>
<body>
<main class="canvas">
  <section class="card card--front" aria-label="Business card front">
    <svg class="front-swoosh" viewBox="0 0 540 309" preserveAspectRatio="none" aria-hidden="true">
      <path d="M0 175 Q40 205 160 232 Q330 268 540 262 L540 309 L0 309 Z" fill="var(--black)"/>
      <path d="M40 185 Q190 250 420 262" fill="none" stroke="var(--blue)" stroke-width="3"/>
    </svg>
    <div class="brand"><span>Flood Rescue 360</span><span class="brand-mark"></span></div>
    <div class="divider"></div>
    <div class="contact">
      <div class="contact__name">Marcus Pelley</div>
      <div class="contact__title">General Manager</div>
      <div class="contact__row"><svg viewBox="0 0 24 24"><path d="M6.6 10.8a15 15 0 0 0 6.6 6.6l2.2-2.2a1 1 0 0 1 1-.25 11.4 11.4 0 0 0 3.6.57 1 1 0 0 1 1 1V20a1 1 0 0 1-1 1A17 17 0 0 1 3 4a1 1 0 0 1 1-1h3.5a1 1 0 0 1 1 1c0 1.25.2 2.45.57 3.57a1 1 0 0 1-.25 1z"/></svg>214-555-0193</div>
      <div class="contact__row"><svg viewBox="0 0 24 24"><path d="M4 9c0-3 4-5 8-5s8 2 8 5v2h-4V9H8v2H4zM6 12h12l2 8H4zm6 2a2.5 2.5 0 1 0 0 5 2.5 2.5 0 0 0 0-5z"/></svg>469-555-0148</div>
      <div class="contact__row"><svg viewBox="0 0 24 24"><path d="M2 5h20v14H2zm2 2v.5l8 5 8-5V7z"/></svg>Marcus@FloodRescue360.example</div>
    </div>
    <div class="services"><span class="dot">•</span>Water<span class="dot">•</span>Fire<span class="dot">•</span>Mold<span class="dot">•</span>Reconstruction</div>
  </section>

  <section class="card card--back" aria-label="Business card back">
    <div class="pattern" role="img" aria-label="Repeating brand-mark pattern in glossy black and grey"></div>
    <div class="tagline"><span>Urgency for Your Water Emergency!</span><span class="tagline__brand"><span class="brand-mark"></span></span></div>
  </section>
</main>
</body>
</html>
```